eBook Cover_H. Lindqvist-Borna
Schnell und zuverlässoig,Änderungswünsche wurden umgehend ausgeführt. Vielen Dank für das tolle Cover zu meinem ersten Buch!
Zielgruppe
freie Roman-Autorin (Erstlingswerk)
Zielgruppe: Lesende (Erwachsene), Frauen
Charakterisierung: magisch-realistischer Familienroman, spielt im Europa der Jetzt-Zeit
Aufgabenstellung
Im ersten Schritt geht es um ein Cover für ein eBook, das aber bei Bedarf als Book on Demand gedruckt werden soll. Es wird daher später Anforderung bzgl. Dicke / Umfang des gedruckten Buches und einer Rückseite geben. Das gewählte Design soll dann dahingehend überarbeitet und finale Druckdaten zur Verfügung gestellt werden. Dies soll von vornherein berücksichtigt werden und im Preis enthalten sein.
Titel: Regen über Glas, Monde im Moos
Autorinnenname: Henrike Lindqvist-Borna
des weiteren auf dem Cover: Roman

```html
<!DOCTYPE html>
<html lang="de">
<head>
<meta charset="utf-8">
<title>Regen über Glas, Monde im Moos – Henrike Lindqvist-Borna</title>
<link rel="stylesheet" href="https://fonts.googleapis.com/css2?family=Parisienne&family=Nunito+Sans:wght@600;700&display=swap">
<style>
  :root {
    --stage: #d9d9d9;
    --paper: #ffffff;
    --cover-red: #c40f14;
    --author-grey: #6a6a6a;
    --title-white: #ffffff;
    --shadow: rgba(0, 0, 0, 0.35);
  }
  * { margin: 0; padding: 0; box-sizing: border-box; }
  html, body {
    width: 841px;
    height: 1200px;
    overflow: hidden;
    background: var(--stage);
  }
  .cover {
    position: absolute;
    left: 45px;
    top: 47px;
    width: 748px;
    height: 1106px;
    background: var(--paper);
    box-shadow: 6px 6px 8px var(--shadow);
    overflow: hidden;
  }
  .cover-shapes {
    position: absolute;
    inset: 0;
    width: 748px;
    height: 1106px;
  }
  .author {
    position: absolute;
    left: 0;
    right: 0;
    top: 125px;
    text-align: center;
    font-family: "Parisienne", cursive;
    font-size: 50px;
    color: var(--author-grey);
    letter-spacing: 1px;
  }
  .title {
    position: absolute;
    left: 0;
    right: 0;
    top: 448px;
    text-align: center;
    font-family: "Nunito Sans", sans-serif;
    font-weight: 700;
    font-size: 70px;
    line-height: 88px;
    color: var(--title-white);
  }
  .genre {
    position: absolute;
    left: 0;
    right: 0;
    top: 858px;
    text-align: center;
    font-family: "Nunito Sans", sans-serif;
    font-weight: 600;
    font-size: 58px;
    letter-spacing: 1px;
    color: var(--title-white);
  }
</style>
</head>
<body>
  <div class="cover">
    <svg class="cover-shapes" viewBox="0 0 748 1106" xmlns="http://www.w3.org/2000/svg">
      <defs>
        <linearGradient id="meadow-tones" x1="0" y1="0" x2="0" y2="1">
          <stop offset="0" stop-color="#3c59b8"/>
          <stop offset="0.12" stop-color="#7fa97a"/>
          <stop offset="0.3" stop-color="#8fce3a"/>
          <stop offset="0.55" stop-color="#b9c832"/>
          <stop offset="0.75" stop-color="#c9b02e"/>
          <stop offset="1" stop-color="#b5432a"/>
        </linearGradient>
      </defs>
      <path class="red-band" d="M0 355 Q374 398 748 355 L748 1106 L0 1106 Z" fill="var(--cover-red)"/>
      <path class="meadow-painting" role="img" aria-label="Gemalte Mohnwiese in Grün, Gelb und Rot unter blauem Himmel"
            d="M0 799 Q374 621 748 799 L748 1106 L0 1106 Z" fill="url(#meadow-tones)"/>
    </svg>
    <p class="author">Henrike Lindqvist-Borna</p>
    <h1 class="title">Regen über Glas<br>Monde im Moos</h1>
    <p class="genre">ROMAN</p>
  </div>
</body>
</html>
```